Need logo and design for business card "FernGlen Plumbing Services".

Needing a design for plumbing company 'FernGlen Plumbing Services', a company based on the surfcoast.
Would like the colour black and blue incorporated. We offer free quotes and reliable friendly service, but don't want this writing on front of card.

I do not have a logo so wanting ideas. Any logo ideas on it would be great.

Target Market(s)

People wanting a Plumber

Industry/Entity Type

Business

Requirements
Must have
• Domestic Plumbing
• Commercial Plumbing
• Roofing
• Gasfitting
Nice to have
• Maybe some sort of plumbing picture on it, spanner, toilet, tap with water etc. Just relating to plumbing.
• FernGlen is on word also with the capital A in it.

```html
<!DOCTYPE html>
<html lang="en">
<head>
<meta charset="utf-8">
<title>FernGlen Plumbing Services – Business Card</title>
<link href="https://fonts.googleapis.com/css2?family=Questrial&family=Didact+Gothic&display=swap" rel="stylesheet">
<style>
  :root {
    --page-bg: #d9d9d9;
    --card-bg: #f4f4f2;
    --brand-blue: #5b93c9;
    --brand-dark: #1f2a36;
    --ink: #1b1b1b;
    --muted: #3c3c3c;
    --photo-light: #e9ecef;
    --photo-mid: #9fb3c8;
    --photo-dark: #2f4b78;
  }
  * { box-sizing: border-box; margin: 0; padding: 0; }
  html, body { width: 1200px; height: 1000px; overflow: hidden; }
  body {
    background: var(--page-bg);
    font-family: "Questrial", "Century Gothic", sans-serif;
    color: var(--ink);
    position: relative;
  }
  .card {
    position: absolute;
    left: 280px;
    width: 640px;
    height: 366px;
    background: var(--card-bg);
    box-shadow: 0 6px 18px rgba(0,0,0,0.18);
    overflow: hidden;
  }
  .card--front { top: 100px; }
  .card--back { top: 520px; }

  /* Front */
  .front-photo {
    position: absolute;
    left: 0; top: 0;
    width: 330px; height: 100%;
    background: linear-gradient(120deg, var(--photo-dark) 0%, var(--photo-mid) 40%, var(--photo-light) 80%, var(--card-bg) 100%);
  }
  .brand {
    position: absolute;
    display: flex;
    align-items: center;
    gap: 10px;
    color: var(--brand-dark);
    font-family: "Questrial", sans-serif;
    font-size: 24px;
    line-height: 1.05;
  }
  .brand__dot {
    width: 16px; height: 16px;
    border-radius: 50%;
    background: var(--brand-blue);
    flex: none;
  }
  .card--front .brand { left: 360px; top: 78px; width: 260px; }
  .services {
    position: absolute;
    left: 382px; top: 170px;
    list-style: none;
    font-family: "Didact Gothic", sans-serif;
    font-size: 21px;
    line-height: 1.2;
    color: var(--ink);
  }

  /* Back */
  .card--back .brand { left: 380px; top: 44px; width: 240px; }
  .person-name {
    position: absolute;
    left: 60px; top: 94px;
    font-size: 40px;
    color: var(--brand-blue);
  }
  .divider {
    position: absolute;
    left: 56px; top: 152px;
    width: 540px; height: 4px;
    background: var(--ink);
  }
  .contact-list {
    position: absolute;
    left: 60px; top: 178px;
    list-style: none;
    font-size: 17px;
    color: var(--muted);
  }
  .contact-list li {
    display: flex;
    align-items: center;
    gap: 12px;
    height: 28px;
  }
  .icon { width: 17px; height: 17px; fill: var(--brand-blue); flex: none; }
  .address {
    position: absolute;
    left: 400px; top: 300px;
    display: flex;
    align-items: flex-start;
    gap: 40px;
    font-size: 18px;
    color: var(--muted);
  }
  .address .icon { width: 18px; height: 22px; margin-top: -14px; }
</style>
</head>
<body>

<section class="card card--front" aria-label="Business card front">
  <div class="front-photo" role="img" aria-label="Photo of a plumber in a blue cap and shirt fitting pipes under a sink with a red pipe wrench"></div>
  <div class="brand">
    <span class="brand__dot"></span>
    <span class="brand__name">FernGlen Plumbing Services</span>
  </div>
  <ul class="services">
    <li>Domestic Plumbing</li>
    <li>Commercial Plumbing</li>
    <li>Roofing</li>
    <li>Gasfitting</li>
  </ul>
</section>

<section class="card card--back" aria-label="Business card back">
  <div class="brand">
    <span class="brand__dot"></span>
    <span class="brand__name">FernGlen Plumbing Services</span>
  </div>
  <h1 class="person-name">John Doe</h1>
  <div class="divider"></div>
  <ul class="contact-list">
    <li>
      <svg class="icon" viewBox="0 0 24 24" aria-hidden="true"><path d="M6.6 10.8a15.5 15.5 0 0 0 6.6 6.6l2.2-2.2c.3-.3.7-.4 1-.2 1.1.4 2.3.6 3.6.6.6 0 1 .4 1 1V20c0 .6-.4 1-1 1A17 17 0 0 1 3 4c0-.6.4-1 1-1h3.5c.6 0 1 .4 1 1 0 1.3.2 2.5.6 3.6.1.3 0 .7-.2 1z"/></svg>
      <span>123.456.7890</span>
    </li>
    <li>
      <svg class="icon" viewBox="0 0 24 24" aria-hidden="true"><path d="M6 2h12v5H6zM4 8h16a2 2 0 0 1 2 2v7h-4v5H6v-5H2v-7a2 2 0 0 1 2-2zm4 8v4h8v-4z"/></svg>
      <span>123.456.7890</span>
    </li>
    <li>
      <svg class="icon" viewBox="0 0 24 24" aria-hidden="true"><path d="M2 5h20v14H2zm2 2v.5l8 5 8-5V7l-8 5z"/></svg>
      <span>yourname@domaine.com</span>
    </li>
    <li>
      <svg class="icon" viewBox="0 0 24 24" aria-hidden="true"><path d="M12 2a10 10 0 1 0 0 20 10 10 0 0 0 0-20zm-1 2.1V8H7.4A8 8 0 0 1 11 4.1zm2 0A8 8 0 0 1 16.6 8H13zM6.4 10H11v4H6.4a8 8 0 0 1 0-4zm6.6 0h4.6a8 8 0 0 1 0 4H13zm-5.6 6H11v3.9A8 8 0 0 1 7.4 16zm5.6 0h3.6a8 8 0 0 1-3.6 3.9z"/></svg>
      <span>www.domaine.com.</span>
    </li>
  </ul>
  <div class="address">
    <svg class="icon" viewBox="0 0 24 30" aria-hidden="true"><path d="M12 0a10 10 0 0 0-10 10c0 7.5 10 20 10 20s10-12.5 10-20A10 10 0 0 0 12 0zm0 14a4 4 0 1 1 0-8 4 4 0 0 1 0 8z"/></svg>
    <span>Your Adresse here</span>
  </div>
</section>

</body>
</html>
```